Buch-/E-Book-Cover im Bereich der Persönlichkeitsentwicklung
Vielen lieben Dank für die super Arbeit von Dir. Das Design ist klasse und die vielen Vorschläge waren auch super. Die komplette Zusammenarbeit verlief sehr professionell und Änderungswünsche wurden sehr schnell umgesetzt. Ich kann Dich voll und ganz weiterempfehlen.
Zielgruppe
Wir arbeiten in der Persönlichkeitsentwicklung für Jugendliche. Dabei spezialisieren wir uns auf den Altersbereich 12 - 17 Jahre. Unser Ziel ist es jungen Menschen zu zeigen, wie Sie zu sich selbst finden und ein glückliches sowie erfolgreiches Leben führen können.
Aufgabenstellung
- Das Design sollte für die Eltern von Teenagern und auch für die Teenager selbst ausgelegt werden. Das Buch ist für die Jugendlichen (Mädchen und Jungen im Alter zwischen 12 Jahren und 17 Jahren) gedacht, wird allerdings meist von deren Mütter gekauft.
- Der Name des Autors lautet: Henrik Falbe
- Der Titel lautet: Junge Herzen finden Mut und Richtung
- Der Untertitel lautet: Was Heranwachsende über ihren Weg lernen
- Im Anhang befinden sich Designs, die ich gut finde (nur falls jemand weitere Ideen haben möchte)
- Format: 15,24 cm x 22,86 cm (6' x 9') [genaue Maße fürs Taschenbuch und Hardcover sind im Anhang (.zip Dateien)]
1. E-Book:
- Coverdateien sollten idealerweise 2 560 Pixel hoch und 1 600 Pixel breit sein. Zur Gewährleistung der bestmöglichen Qualität (insbesondere auf HD-Geräten) sollte das Bild mindestens 2 500 Pixel hoch sein.
- Format: TIFF (.tif/.tiff) oder JPEG (.jpeg/.jpg)
- DPI: 72 dpi
- Größe: Ihr Coverbild muss kleiner als 50 MB sein.
Hinweis: Vermeiden Sie es, Ihre Dateien zu komprimieren. Dies kann die Qualität Ihres Covers auf Lesegeräten beeinträchtigen. Das beste Ergebnis erzielen Sie mit Bildern, die eine Mindestauflösung von 300 ppi (Pixels per Inch) haben.
- Rahmen: Coverbilder mit weißem oder sehr hellem Hintergrund heben sich kaum vom weißen Hintergrund ab. Fügen Sie einen dünnen Rahmen (3–4 Pixel) in Mittelgrau hinzu, um die Ränder des Covers besser sichtbar zu machen.
2. + 3. Taschenbuch/Hardcover [genaue Maße fürs Taschenbuch und Hardcover sind im Anhang (.zip Dateien)] :
- Dateityp: Das Cover muss als einzelne PDF-Datei vorliegen und die hintere Coverseite, den Buchrücken und die vordere Coverseite als einzelnes Bild enthalten.
- Dateigröße: Coverdateien, die größer als 650 MB sind, können nicht konvertiert werden. Die Datei sollte maximal 40 MB groß sein, da sich bei großen Dateien der Druck verlangsamt.
- Die gen..

```html
<!DOCTYPE html>
<html lang="de">
<head>
<meta charset="utf-8">
<title>Junge Herzen finden Mut und Richtung – Henrik Falbe</title>
<link rel="stylesheet" href="https://fonts.googleapis.com/css2?family=Londrina+Solid:wght@300;900&family=Zilla+Slab:wght@500;600&display=swap">
<style>
  :root {
    --page: #ffffff;
    --frame: #9a9a9a;
    --ink: #1d1d1b;
    --magenta: #b8004f;
    --navy: #1f4f7c;
    --tone-grey: #b4b4b4;
    --tone-blue: #c3d2ec;
  }
  * { margin: 0; padding: 0; box-sizing: border-box; }
  html, body {
    width: 1200px; height: 1200px; overflow: hidden;
    background: var(--page);
  }
  .cover {
    position: absolute;
    left: 245px; top: 70px;
    width: 724px; height: 1086px;
    border: 2px solid var(--frame);
    background: var(--page);
  }
  .author {
    position: absolute; left: 0; right: 0; top: 38px;
    text-align: center;
    font-family: "Zilla Slab", serif;
    font-weight: 600; font-size: 34px; letter-spacing: 3px;
    color: var(--ink);
    text-transform: uppercase;
  }
  .summit-illustration {
    position: absolute; left: 194px; top: 142px;
    width: 357px; height: 358px;
    border-radius: 8px;
    background: linear-gradient(135deg, var(--tone-grey), var(--tone-blue));
  }
  .title-word {
    position: absolute;
    font-family: "Londrina Solid", sans-serif;
    font-weight: 900; line-height: 1;
    color: var(--magenta);
    white-space: nowrap;
  }
  .title-link {
    position: absolute;
    font-family: "Londrina Solid", sans-serif;
    font-weight: 300; line-height: 1;
    color: var(--navy);
    white-space: nowrap;
  }
  .word-herzen { left: 0; right: 0; text-align: center; top: 510px; font-size: 106px; }
  .word-finden { right: 296px; top: 663px; font-size: 64px; }
  .word-mut { left: 62px; top: 700px; font-size: 150px; }
  .word-und { right: 296px; top: 722px; font-size: 64px; }
  .word-richtung { right: 66px; top: 773px; font-size: 102px; }
  .subtitle {
    position: absolute; right: 298px; top: 875px;
    text-align: right;
    font-family: "Zilla Slab", serif;
    font-weight: 500; font-size: 30px; line-height: 45px;
    color: var(--navy);
    white-space: nowrap;
  }
  .subtitle span { display: block; }
  .subtitle .lead-line { padding-right: 124px; }
</style>
</head>
<body>
  <main class="cover">
    <p class="author">Henrik Falbe</p>

    <div class="summit-illustration" role="img" aria-label="Illustration: zwei Jugendliche mit Fahne auf einem Berggipfel zwischen Wolken und Tannen"></div>

    <h1 class="title">
      <span class="title-word word-herzen">Junge Herzen</span>
      <span class="title-link word-finden">finden</span>
      <span class="title-word word-mut">Mut</span>
      <span class="title-link word-und">und</span>
      <span class="title-word word-richtung">Richtung</span>
    </h1>

    <p class="subtitle">
      <span class="lead-line">Was Heranwachsende</span>
      <span>über ihren Weg</span>
      <span>lernen</span>
    </p>
  </main>
</body>
</html>
```